Marlow's Tide Kitchen

Marlow’s Tide Kitchen

This project is a design of a restaurant referral card used for tourist and business travelers. It needs to be 2 sided, 4/1 front color, grayscale back. I am including the specs ie, the size of the card as well as a sample card. I am also including the some pics and text. I would like a few looks for this card.

I need a card with front and back with the following specs:

• Card size 4 inch height x 2 1/8 inch width
• Top: ¾ inch Logo/header on front of card
• Front: four color
• Back: Grayscale/ black and white
* FULL Bleed for print
***Note the logo needs to be at the top 3/4 inch on the front of the card***
Front of Card:
~Logo/Restaurant name “Marlow’s Tide Kitchen” (top ¾ inch of card front)
~Marlow’s seafood is flown in daily from New England. It is our goal to serve the freshest seafood available in the Traditional New England style.

~Family Owned and operated
~ Take Out Available
~572-918-3346
~Open 7 days a week 11AM-8:00PM
~2730 W Harbor Rd Bayhaven Shores FL

www.marlowstidekitchenqrp.example
~KIDS MENU $5.99

Back of Card:
~Logo/Restaurant name “Marlow’s Tide Kitchen”
~ Freshest seafood available in the Traditional New England style
~Specialties include: Haddock, Cod, Mahi, Flounder, Fried Oysters, Whole Belly Clams, NE Steamers, Crab Legs, Lobster Salad, & much more!!
~Map (included)
~572-918-3346
~Located on Route 9

Please note you can add your own flare and verbage just need the highlighted points/text above to be the focus. Would like to highlight the Fresh Seafood aspect of this restaurant. BE CREATIVE
PS I attached a sample card of front and back for specs from another card.
Also would like to see sample of card with green background similar to green in logo
Thanks,
Gerald
Updates

Industry/Entity Type

Restaurant

Colors
9bcb3c

```html
<!DOCTYPE html>
<html lang="en">
<head>
<meta charset="utf-8">
<title>Marlow’s Tide Kitchen – Referral Card Back</title>
<link rel="stylesheet" href="https://fonts.googleapis.com/css2?family=Oswald:wght@500;700&family=Noto+Serif:wght@400&family=Cabin+Condensed:wght@600&display=swap">
<style>
  :root {
    --ink: #111111;
    --paper: #ffffff;
    --banner-grey: #d4d4d4;
    --box-grey: #cfcfcf;
    --header-dark: #1c1c1c;
    --scene-light: #9a9a9a;
    --scene-mid: #6e6e6e;
    --scene-dark: #2e2e2e;
    --map-land: #dcdcdc;
    --map-water: #7a7a7a;
  }
  html, body {
    margin: 0;
    padding: 0;
    width: 1200px;
    height: 2259px;
    overflow: hidden;
    background: var(--paper);
  }
  .card {
    position: relative;
    width: 1200px;
    height: 2259px;
    overflow: hidden;
    background: var(--paper);
  }
  .dining-room {
    position: absolute;
    inset: 0;
    background: linear-gradient(180deg, var(--scene-light) 0%, var(--scene-mid) 40%, var(--scene-mid) 62%, var(--scene-dark) 100%);
  }
  .corner-curve {
    position: absolute;
    top: 0;
    left: 0;
    width: 1200px;
    height: 700px;
  }
  .brand-name {
    position: absolute;
    left: 50px;
    top: 412px;
    margin: 0;
    color: var(--ink);
    font-weight: 400;
  }
  .brand-name span { display: block; white-space: nowrap; }
  .brand-main {
    font-family: "Oswald", sans-serif;
    font-weight: 700;
    font-size: 128px;
    line-height: 140px;
    letter-spacing: 1px;
  }
  .brand-sub {
    margin-left: 200px;
    margin-top: -8px;
    font-family: "Noto Serif", serif;
    font-size: 58px;
    line-height: 66px;
  }
  .tagline-banner {
    position: absolute;
    left: 212px;
    top: 630px;
    width: 960px;
    height: 186px;
  }
  .tagline-banner svg { position: absolute; inset: 0; }
  .tagline-text {
    position: absolute;
    inset: 18px 20px 0 40px;
    margin: 0;
    font-family: "Noto Serif", serif;
    font-size: 50px;
    line-height: 66px;
    text-align: center;
    color: var(--ink);
  }
  .specialties {
    position: absolute;
    left: 85px;
    top: 940px;
    width: 1060px;
  }
  .specialties-heading {
    margin: 0;
    height: 110px;
    background: var(--header-dark);
    color: var(--paper);
    font-family: "Noto Serif", serif;
    font-weight: 400;
    font-size: 64px;
    line-height: 108px;
    text-align: center;
  }
  .specialties-list {
    margin: 0;
    height: 263px;
    box-sizing: border-box;
    padding-top: 14px;
    background: var(--box-grey);
    font-family: "Cabin Condensed", sans-serif;
    font-weight: 600;
    font-size: 57px;
    line-height: 78px;
    text-align: center;
    color: var(--ink);
  }
  .location-map {
    position: absolute;
    left: 147px;
    top: 1375px;
    width: 912px;
    height: 523px;
    box-sizing: border-box;
    border: 10px solid var(--paper);
    background: linear-gradient(100deg, var(--map-land) 0%, var(--map-land) 62%, var(--map-water) 72%, var(--map-land) 82%, var(--map-land) 100%);
  }
  .contact-band {
    position: absolute;
    left: 0;
    top: 1905px;
    width: 1200px;
    height: 354px;
  }
  .contact-band svg { position: absolute; inset: 0; }
  .contact-lines {
    position: absolute;
    left: 0;
    right: 0;
    top: 22px;
    margin: 0;
    font-family: "Oswald", sans-serif;
    font-weight: 700;
    font-size: 64px;
    line-height: 78px;
    text-align: center;
    color: var(--ink);
  }
  .contact-lines span { display: block; }
</style>
</head>
<body>
<main class="card">
  <div class="dining-room" role="img" aria-label="Photo of the restaurant dining room with booths and tables"></div>

  <svg class="corner-curve" viewBox="0 0 1200 700" aria-hidden="true">
    <path d="M750 0 C690 220 700 500 610 612 L1200 565 L1200 0 Z" fill="var(--paper)"/>
  </svg>

  <h1 class="brand-name">
    <span class="brand-main">MARLOW’S</span>
    <span class="brand-sub">Tide Kitchen</span>
  </h1>

  <div class="tagline-banner">
    <svg viewBox="0 0 960 186" aria-hidden="true">
      <polygon points="22,12 958,0 950,186 0,176" fill="#555"/>
      <polygon points="14,4 944,0 938,172 6,164" fill="var(--banner-grey)" stroke="#333" stroke-width="3"/>
    </svg>
    <p class="tagline-text">Freshest seafood available in the<br>Traditional New England style</p>
  </div>

  <section class="specialties">
    <h2 class="specialties-heading">Specialties include:</h2>
    <p class="specialties-list">Haddock, Cod, Mahi, Flounder, Fried<br>Oysters, Whole Belly Clams, NE Steamers,<br>Crab Legs, Lobster Salad, &amp; much more!!</p>
  </section>

  <div class="location-map" role="img" aria-label="Street map showing the restaurant's location near the coast"></div>

  <footer class="contact-band">
    <svg viewBox="0 0 1200 354" aria-hidden="true">
      <polygon points="0,18 1200,0 1200,354 0,354" fill="var(--paper)"/>
    </svg>
    <p class="contact-lines">
      <span>2730 W Harbor Rd Bayhaven Shores FL</span>
      <span>572-918-3346</span>
      <span>Located on Route 9</span>
    </p>
  </footer>
</main>
</body>
</html>
```